Branding product image: VELMOT (Golden Papaya) in Plastic Cup (Ready to Eat)

The product is sliced Fruit in Light syrup
Flavour: VELMOT (Golden Papaya)
The temporary product name: VELMOT
I want the product design to be something 'fun', 'natural', and 'colourful'
The design concept could be anything depends on your imagination, but it must be eye catchy and attractive.
Basically, I want you to be creative in designing the logo and the overall graphic design for the label.
The measurement is 20 cm (Length) x 6,5 cm (Height)
The target customers are young and health conscious audiences (10 years - 65 years old).
Create something different. Something extraordinary.
Brief summary about the fruit:
This fruit only grows in certain part of the world. It grows in mountain area that is in tropical climate. The fruit flesh has a yellowish-golden color. It has an extraordinary taste (unlike normal papaya) and it suits very well with any dishes from cold appetizer, white/ red meat, desserts, and cocktails.
I need a packaging design for Fruit Cup productThe product is sliced Fruit in Light syrup.There will be various flavours i.e. apple, lychee, peach, papaya, etc.However, you may design the product using one sample flavour (i.e. papaya) first, as the designs of other flavours could be adjusted afterwards.The temporary product name is: RICCANAI want the product design to be something 'fun', 'natural', and 'colourful'.The design concept could be anything depends on your imagination. Basically, I want you to be creative in designing the logo and the overall graphic design for the label. - Create something different. Something extraordinary -Additional:The measurement is 20cm (Length) x 5cm (Height).The target customers are young audiences (10 years - 35 years old).The product design must stand out in the supermarket shelf.It must be eye catchy and attractive.Thank you,Jordan-PLEASE REFER TO DESIGN SAMPLE ATTACHED TO HAVE A BETTER UNDERSTANDING FOR THE PRODUCT CONCEPT- Added Wednesday, September 17, 2014
Project Deadline Extended Reason: Haven't found a good design. Added Friday, September 19, 2014
Project Deadline Extended Reason: Need more time for designers to finalize and perfect the design.Thank you,Jordan Added Monday, September 29, 2014
Project Deadline Extended Reason: I haven't found a great design yet. Added Tuesday, February 24, 2015
Reason: Getting better designs now. Still Open to new ideas while refining the latest designs from some designers.
Please do your best in submitting other great designs!

```html
<!DOCTYPE html>
<html lang="en">
<head>
<meta charset="utf-8">
<title>DOSUVEL Golden Papaya – Cup Label</title>
<link rel="stylesheet" href="https://fonts.googleapis.com/css2?family=Ubuntu:wght@500&family=Courgette&family=Open+Sans:wght@400&display=swap">
<style>
  :root {
    --stage: #eceeed;
    --plum: #6b1f63;
    --plum-deep: #55174f;
    --plum-line: #7d2e74;
    --mist: #f3f8ec;
    --leaf-light: #d9ebc4;
    --leaf: #a9d07a;
    --band-green: #9cc86a;
    --papaya-flesh: #f2a23a;
    --papaya-skin: #e7b02b;
    --white: #ffffff;
  }
  * { margin: 0; padding: 0; box-sizing: border-box; }
  html, body {
    width: 1200px;
    height: 679px;
    overflow: hidden;
    background: var(--stage);
  }
  .canvas {
    position: relative;
    width: 1200px;
    height: 679px;
  }
  .label {
    position: absolute;
    left: 100px;
    top: 140px;
    width: 1000px;
    height: 400px;
    overflow: hidden;
    background: var(--mist);
  }
  .label__top-band {
    position: absolute;
    left: 0; top: 0;
    width: 100%;
    height: 22px;
    background: var(--plum);
  }
  .label__backdrop {
    position: absolute;
    left: 0; top: 22px;
    width: 100%;
    height: 308px;
    background:
      radial-gradient(ellipse 120px 90px at 3% 30%, var(--leaf) 0%, transparent 70%),
      radial-gradient(ellipse 130px 110px at 96% 25%, var(--leaf) 0%, transparent 70%),
      radial-gradient(ellipse 360px 40px at 50% 4%, var(--leaf-light) 0%, transparent 80%),
      linear-gradient(180deg, var(--mist) 0%, #eef6e2 60%, var(--leaf-light) 100%);
  }
  .label__green-rule {
    position: absolute;
    left: 0; top: 330px;
    width: 100%;
    height: 6px;
    background: var(--band-green);
  }
  .label__bottom-band {
    position: absolute;
    left: 0; top: 336px;
    width: 100%;
    height: 64px;
    background: var(--plum);
  }
  .label__bottom-band svg { display: block; }
  .brand-name {
    position: absolute;
    left: 0; top: 60px;
    width: 100%;
    text-align: center;
    font-family: "Ubuntu", sans-serif;
    font-weight: 500;
    font-size: 150px;
    line-height: 1;
    letter-spacing: 2px;
    color: var(--plum);
  }
  .flavour {
    position: absolute;
    left: 112px;
    top: 226px;
    font-family: "Courgette", cursive;
    font-size: 34px;
    line-height: 1.2;
    color: var(--plum);
  }
  .fruit-photo {
    position: absolute;
    left: 438px;
    top: 218px;
    width: 340px;
    height: 150px;
    border-radius: 50% / 50%;
    background: radial-gradient(ellipse at 55% 45%, var(--papaya-flesh) 0%, var(--papaya-skin) 75%, #d79a22 100%);
  }
  .net-weight {
    position: absolute;
    left: 122px;
    top: 356px;
    font-family: "Open Sans", sans-serif;
    font-size: 22px;
    color: var(--white);
  }
</style>
</head>
<body>
<main class="canvas">
  <section class="label">
    <div class="label__top-band"></div>
    <div class="label__backdrop" role="img" aria-label="Soft green bokeh backdrop with fresh leaves along the top and sides"></div>
    <div class="label__green-rule"></div>
    <div class="label__bottom-band">
      <svg width="1000" height="64" viewBox="0 0 1000 64" aria-hidden="true">
        <g stroke="var(--plum-line)" stroke-width="2">
          <line x1="0" y1="14" x2="1000" y2="14"/>
          <line x1="0" y1="30" x2="1000" y2="30"/>
          <line x1="0" y1="46" x2="1000" y2="46"/>
        </g>
      </svg>
    </div>
    <h1 class="brand-name">DOSUVEL</h1>
    <p class="flavour">Golden Papaya<br>in Light Syrup</p>
    <div class="fruit-photo" role="img" aria-label="Two golden papaya halves showing orange flesh and dark seeds"></div>
    <p class="net-weight">Net WT 6oz(170g)</p>
  </section>
</main>
</body>
</html>
```